How likely are people to engage in social distancing? We need a good illustration to show the data!

We surveyed U.S. adults March 20th - 24th, 2020 and asked how likely they were to engage in social distancing (and other COVID-19 related health behaviors). What did the survey find? Basically, most people intend to engage in social distancing behaviors (e.g., avoiding large crowds) and other behaviors that reduce the spread of COVID-19 (e.g., washing hands at least 20 seconds). When most people intend to engage in a behavior, then public health professionals try to leverage that to move more people to act.
Now we need innovative and professional images that attempt to communicate one or all of these findings. The specific findings are nicely summarized in the attached document. For example, 82% of participants intend to engage in social distancing.
What sort of visual are we looking for? Our preference is for an original illustration (or set of illustrations). Our preference is for (creative and powerful illustrations, but we are also open to the creative and well-executed infographics.
We need these images fast . We will award monetary prizes to the 3 best designs. If we like more than that, then we might purchase more (e.g., in past contests, we have purchased as many as 30 designs).
What we will need:
(1) The illustrations must be original and we will need the photoshop and/or illustrator files for all artwork.
(2) You can illustrate all of the findings or just one of them. We need creative approaches that do a lucid job of bringing the data to life. Most people intend to engage in these behaviors. How to communicate that? Republicans and Democrats do not differ in their intentions; how to communicate that?
(3) The illustration should say, somewhere: "Based on a survey of 400 U.S. adults conducted March 20 - 24th, 2020."

U.S. Adults

• Original illustrations based on the findings of the survey (see attached document).

```html
<!DOCTYPE html>
<html lang="en">
<head>
<meta charset="utf-8">
<title>Social Distancing Intentions Survey</title>
<link rel="stylesheet" href="https://fonts.googleapis.com/css2?family=Roboto:wght@400;700;900&display=swap">
<style>
  :root {
    --blue: #1b73c8;
    --blue-dark: #135da6;
    --red: #d8262f;
    --ink: #1d1d1f;
    --grey: #6b6b70;
    --paper: #ffffff;
    --scene-a: #f1f1f3;
    --scene-b: #d9dbe0;
  }
  * { box-sizing: border-box; margin: 0; padding: 0; }
  html, body { width: 1200px; height: 2400px; overflow: hidden; background: var(--paper); }
  body { font-family: "Roboto", Arial, sans-serif; color: var(--ink); }
  .poster { position: relative; width: 1200px; height: 2400px; overflow: hidden; }

  .header {
    position: absolute; left: 0; top: 0; width: 1200px; height: 248px;
    background: var(--blue); padding: 14px;
  }
  .header-frame {
    width: 100%; height: 100%; border: 5px solid var(--paper);
    display: flex; flex-direction: column; justify-content: center; align-items: center;
    color: var(--paper); font-weight: 700; font-size: 62px; line-height: 1.18; text-align: center;
  }

  .intent-title {
    position: absolute; left: 0; top: 272px; width: 1200px;
    text-align: center; font-weight: 900; font-size: 60px; line-height: 1.08;
  }
  .intent-list { position: absolute; left: 0; top: 418px; width: 1200px; list-style: none; }
  .intent-list li {
    height: 45px; padding-left: 40px; font-size: 37px; line-height: 45px; white-space: nowrap;
  }
  .intent-list li:nth-child(odd) { background: var(--red); color: var(--paper); }

  .compare-band {
    position: absolute; left: 0; top: 792px; width: 1200px; height: 108px;
    background: var(--blue); color: var(--paper);
    font-weight: 900; font-size: 60px; line-height: 108px; text-align: center;
  }
  .legend {
    position: absolute; left: 0; top: 918px; width: 1200px;
    display: flex; justify-content: center; gap: 36px; font-size: 30px; color: var(--grey);
  }
  .legend span { display: flex; align-items: center; gap: 10px; }
  .legend i { display: inline-block; width: 26px; height: 26px; }
  .swatch-rep { background: var(--red); }
  .swatch-dem { background: var(--blue); }

  .scene {
    position: absolute; left: 120px; top: 972px; width: 960px; height: 610px;
    background: radial-gradient(ellipse at center, var(--scene-a), var(--scene-b));
    border-radius: 12px;
  }

  .chart { position: absolute; left: 0; top: 1590px; width: 1200px; height: 600px; }
  .chart text { font-family: "Roboto", Arial, sans-serif; }
  .chart .label { font-size: 21px; fill: var(--ink); }
  .chart .tick { font-size: 24px; fill: var(--ink); }

  .takeaway {
    position: absolute; left: 0; top: 2188px; width: 1200px; height: 116px;
    background: var(--blue); color: var(--paper);
    font-weight: 900; font-size: 44px; line-height: 1.12; text-align: center;
    display: flex; align-items: center; justify-content: center;
  }
  .footer {
    position: absolute; left: 0; top: 2304px; width: 1200px; height: 96px;
    display: flex; align-items: center; justify-content: space-between; padding: 0 40px 0 60px;
  }
  .footer-note { font-size: 26px; color: var(--ink); }
  .brand { display: flex; align-items: center; gap: 14px; }
  .brand-mark { width: 56px; height: 56px; background: var(--red); }
  .brand-name { font-weight: 700; font-size: 26px; line-height: 1.05; color: var(--ink); text-transform: uppercase; }
</style>
</head>
<body>
<main class="poster">
  <header class="header">
    <div class="header-frame">
      <p>Survey of U.S. Adults (N = 400)</p>
      <p>conducted March 20th - 24th, 2020</p>
    </div>
  </header>

  <h1 class="intent-title">Percent of Americans intending<br>to engage in social distancing</h1>
  <ul class="intent-list">
    <li>Engage in social distancing: 82% intend to</li>
    <li>Work from home: 63% intend to</li>
    <li>Avoid large gatherings: 85% intend to</li>
    <li>Cancel social activities: 81% intend to</li>
    <li>Put distance between yourself and other people: 85% intend to</li>
    <li>Wash hands at least 20 seconds: 87% intend to</li>
    <li>Use hand sanitizer: 85% intend to</li>
    <li>Avoid touching your eyes, nose, and mouth: 81% intend to</li>
  </ul>

  <h2 class="compare-band">Comparing Republicans and Democrats</h2>
  <div class="legend">
    <span><i class="swatch-rep"></i>Republican</span>
    <span><i class="swatch-dem"></i>Democrat</span>
  </div>

  <div class="scene" role="img" aria-label="Illustration of elephants and donkeys keeping six feet apart: working at laptops, washing hands and using sanitizer"></div>

  <svg class="chart" viewBox="0 0 1200 600" width="1200" height="600">
    <g stroke="#c9c9cc" stroke-width="2">
      <line x1="312" y1="10" x2="312" y2="530"/>
      <line x1="514" y1="10" x2="514" y2="530"/>
      <line x1="716" y1="10" x2="716" y2="530"/>
      <line x1="918" y1="10" x2="918" y2="530"/>
      <line x1="1120" y1="10" x2="1120" y2="530"/>
      <line x1="312" y1="530" x2="1120" y2="530"/>
    </g>
    <g class="tick" text-anchor="middle">
      <text x="312" y="566">0%</text>
      <text x="514" y="566">25%</text>
      <text x="716" y="566">50%</text>
      <text x="918" y="566">75%</text>
      <text x="1120" y="566">100%</text>
    </g>
    <g class="label" text-anchor="end">
      <text x="290" y="38">Engage in social</text><text x="290" y="61">distancing</text>
      <text x="290" y="112">Work from home</text>
      <text x="290" y="166">Avoid large</text><text x="290" y="189">gatherings</text>
      <text x="290" y="230">Cancel social</text><text x="290" y="253">activities</text>
      <text x="290" y="282">Put distance between</text><text x="290" y="304">yourself and other</text><text x="290" y="326">people</text>
      <text x="290" y="358">Wash hands at least</text><text x="290" y="381">20 seconds</text>
      <text x="290" y="432">Use hand sanitizer</text>
      <text x="290" y="474">Avoid touching your</text><text x="290" y="496">eyes, nose, and</text><text x="290" y="518">mouth</text>
    </g>
    <g fill="var(--red)">
      <rect x="312" y="26" width="663" height="16"/>
      <rect x="312" y="90" width="485" height="16"/>
      <rect x="312" y="154" width="695" height="16"/>
      <rect x="312" y="218" width="663" height="16"/>
      <rect x="312" y="282" width="679" height="16"/>
      <rect x="312" y="346" width="703" height="16"/>
      <rect x="312" y="410" width="695" height="16"/>
      <rect x="312" y="474" width="663" height="16"/>
    </g>
    <g fill="var(--blue)">
      <rect x="312" y="42" width="646" height="16"/>
      <rect x="312" y="106" width="533" height="16"/>
      <rect x="312" y="170" width="679" height="16"/>
      <rect x="312" y="234" width="646" height="16"/>
      <rect x="312" y="298" width="703" height="16"/>
      <rect x="312" y="362" width="711" height="16"/>
      <rect x="312" y="426" width="679" height="16"/>
      <rect x="312" y="490" width="663" height="16"/>
    </g>
  </svg>

  <section class="takeaway">
    <p>What does this data show? No big differences.<br>Basically the same patterns.</p>
  </section>

  <footer class="footer">
    <p class="footer-note">Based on a survey of 400 U.S. adults conducted March 20 - 24th, 2020</p>
    <div class="brand">
      <span class="brand-mark"></span>
      <span class="brand-name">Northfield<br>University</span>
    </div>
  </footer>
</main>
</body>
</html>
```